New Business Card Design for Manufacturing

We are an engineering/manufacturing company that offers Advanced machining/assembly/engineering services, as well as innovative products for the heavy duty engine cooling markets.

We are looking to get a new business card designed that is clean and modern looking, but still fits the wide range of technical/skilled work we do.

- We hope to use this design as the base for other design work in new Presentations, web, and print work.

Industry/Entity Type

Engineering

Contact Information for Business Card

Our preferred color of blue is (RGB) 22/71/159 but can vary slightly from that color. Our content will be our Logo and full company name (Vantrell Forge Works, Inc.), company address, name, job title, phone number with extension, cell number, fax number, website, and email address on the cards.
We'd like the full company name next to the logo, but we are open to other interpretations of that layout.
Preferably, we would like the back side to be clean with just our logo, and the front to contain all of the contact information.

Colors
2f74b4
0355a3
85abd2

Requirements
Must have
• - Logo, company name, needed content - We are open to interpretation beyond that.
• - Standard size business card.
• - Horizontal orientation.
• - Enough space for lengthy names / job titles (for example, a job title could read "Directory of Human Resources" or "V.P. of Governmental Affairs"). We need this to look clean, whether the title be short (CEO) or long (as described above).

```html
<!DOCTYPE html>
<html lang="en">
<head>
<meta charset="utf-8">
<title>Vantrell Forge Works – Business Card</title>
<link rel="stylesheet" href="https://fonts.googleapis.com/css2?family=Montserrat:wght@400;600;700;800&display=swap">
<style>
  :root {
    --brand-blue: #16479f;
    --steel-grey: #8a8d91;
    --text-grey: #6d7074;
    --rule-grey: #b9bcc0;
    --card-white: #ffffff;
    --card-black: #1d1d1e;
    --mark-dark: #2e2e30;
    --backdrop: #e9eaec;
  }
  * { box-sizing: border-box; margin: 0; padding: 0; }
  html, body {
    width: 1200px; height: 794px; overflow: hidden;
    background: var(--backdrop);
    font-family: "Montserrat", sans-serif;
  }
  .sheet {
    position: relative; width: 1200px; height: 794px;
    display: flex; align-items: center; justify-content: center; gap: 30px;
  }
  .card {
    position: relative; width: 540px; height: 309px; overflow: hidden;
    box-shadow: 0 4px 14px rgba(0,0,0,.12);
  }

  /* Back side */
  .card-back { background: var(--card-black); }
  .card-back .wordmark {
    position: absolute; left: 0; right: 0; top: 118px;
    text-align: center; font-weight: 800; font-size: 30px;
    color: var(--mark-dark); letter-spacing: .5px;
  }
  .card-back .web {
    position: absolute; left: 0; right: 0; top: 232px;
    text-align: center; font-size: 10px; color: #5a5a5c; letter-spacing: .3px;
  }

  /* Front side */
  .card-front { background: var(--card-white); }
  .card-front .wordmark {
    position: absolute; right: 34px; top: 44px;
    font-weight: 800; font-size: 22px; color: var(--brand-blue);
  }
  .card-front .top-rule {
    position: absolute; left: 230px; right: 30px; top: 92px;
    height: 1px; background: var(--rule-grey);
  }
  .address {
    position: absolute; right: 30px; top: 140px; text-align: right;
    font-size: 10.5px; line-height: 1.55; color: var(--text-grey);
  }
  .person { position: absolute; left: 32px; top: 150px; }
  .person .name { font-weight: 700; font-size: 17px; color: var(--brand-blue); }
  .person .title { font-size: 10.5px; color: var(--text-grey); margin-top: 3px; }
  .person .rule { width: 220px; height: 1px; background: var(--rule-grey); margin-top: 7px; }
  .contacts { list-style: none; margin-top: 7px; }
  .contacts li {
    display: flex; align-items: center; gap: 8px;
    font-size: 10px; line-height: 15px; color: var(--text-grey);
  }
  .contacts svg { width: 9px; height: 9px; fill: var(--brand-blue); flex: none; }

  .accent-band {
    position: absolute; right: 0; bottom: 20px; width: 300px; height: 9px;
    background: var(--steel-grey); border-top-left-radius: 9px;
  }
  .footer-band {
    position: absolute; left: 0; right: 0; bottom: 0; height: 20px;
    background: var(--brand-blue);
    display: flex; align-items: center; padding-left: 32px;
    font-size: 10px; color: var(--card-white); letter-spacing: .2px;
  }
</style>
</head>
<body>
<main class="sheet">

  <section class="card card-back" aria-label="Business card, back">
    <div class="wordmark">Vantrell Forge Works</div>
    <div class="web">www.yourmailaddress.com</div>
  </section>

  <section class="card card-front" aria-label="Business card, front">
    <div class="wordmark">Vantrell Forge Works</div>
    <div class="top-rule"></div>

    <address class="address" style="font-style:normal">
      Street Name Avenue, Suite 100<br>
      State, Zip Code,Country
    </address>

    <div class="person">
      <div class="name">Marcus Hollen</div>
      <div class="title">President</div>
      <div class="rule"></div>
      <ul class="contacts">
        <li>
          <svg viewBox="0 0 10 10" aria-hidden="true"><path d="M2 0.5 L3.6 2.6 L2.7 3.6 Q3.6 5.8 6.4 7.3 L7.4 6.4 L9.5 8 L8.3 9.5 Q1.8 8.3 0.5 1.7 Z"/></svg>
          +000.000.00 00
        </li>
        <li>
          <svg viewBox="0 0 10 10" aria-hidden="true"><path d="M2.5 0 H7.5 V10 H2.5 Z M3.3 1.2 V7.8 H6.7 V1.2 Z"/><circle cx="5" cy="8.9" r=".5" fill="#fff"/></svg>
          +000.000.00 00
        </li>
        <li>
          <svg viewBox="0 0 10 10" aria-hidden="true"><path d="M2.5 0 H7.5 V3 H2.5 Z M0.5 3.5 H9.5 V7.5 H8 V6 H2 V7.5 H0.5 Z M2.8 6.6 H7.2 V10 H2.8 Z"/></svg>
          +000.000.00 00
        </li>
        <li>
          <svg viewBox="0 0 10 10" aria-hidden="true"><path d="M0 1.5 H10 V8.5 H0 Z M0.6 2 L5 5.6 L9.4 2 Z" fill-rule="evenodd"/></svg>
          www.yourmailaddress.com
        </li>
      </ul>
    </div>

    <div class="accent-band"></div>
    <div class="footer-band">www.yourmailaddress.com</div>
  </section>

</main>
</body>
</html>
```